Brackwell Exteriors Needs a New Website!

We are an exteriors company specializing in vinyl siding, Corwin Maddox siding, aluminum soffit/fascia, trough. We do new construction work as well as renovations. We also build detached garages.
You can view our current website at www.brackwellfabricators.ca
I want to completely overhaul the website.
Our services are different now as we no longer do new home construction as well as we do not do the snow clearing.
I want to focus on 2 things in particular on the website:

1/ Exterior renovations

2/ Detached Garage construction.

I have included our logo in the attached files to use as well.

Some features we would like:

1/ Be able to easily attach a video from Clipverse/Reelio to highlight a product or service
2/ Quick chat or contact button that we can talk to a potential client quickly
3/ Meet the Team page that is interesting and fresh
4/ Place for us to put in helpful exterior tips/suggestions for homeowners.

Content is not important, but looking for the best design that will attract people once they click on our page and want to renovate with us.

Target Market(s)

People looking for renovations on their home, people looking to build a detached garage.

Industry/Entity Type

Residential Construction

Number of Pages Required

5+ page

Font styles to use
Sans Serif

Requirements
Must have
• Fresh and exciting home page.

Simple design. Don't want it over complicated or too much information to confuse the potential client.

Easy way to contact us.

Meet the team page that instills confidence
Nice to have
• Colour of website to go off our logo. Doesn't need to be an exact match, but something that goes well with our blue and grey.

```html
<!DOCTYPE html>
<html lang="en">
<head>
<meta charset="utf-8">
<title>Brackwell Exteriors</title>
<link href="https://fonts.googleapis.com/css2?family=Montserrat:wght@400;500;600;700&family=Open+Sans:wght@400;600&display=swap" rel="stylesheet">
<style>
:root{
  --blue:#0a6cc2;
  --blue-dark:#08559a;
  --ink:#111418;
  --text:#4a4f55;
  --muted:#7a8087;
  --pale:#eef5fc;
  --line:#dfe3e8;
  --footer:#1d2125;
  --white:#fff;
}
*{box-sizing:border-box;margin:0;padding:0}
html,body{width:1200px;height:4812px;overflow:hidden}
body{position:relative;background:var(--white);font-family:"Montserrat",sans-serif;color:var(--ink)}
.abs{position:absolute}
.btn{position:absolute;display:flex;align-items:center;justify-content:center;font:600 12px "Montserrat",sans-serif;letter-spacing:.6px;text-transform:uppercase;height:38px}
.btn-solid{background:var(--blue);color:var(--white)}
.btn-line{border:1.5px solid var(--blue);color:var(--blue);background:var(--white)}
.heading{position:absolute;left:0;width:1200px;text-align:center;font:700 29px "Montserrat",sans-serif;letter-spacing:.5px}
.heading span{color:var(--blue)}
.heading::after{content:"";display:block;width:64px;height:2px;background:var(--blue);margin:14px auto 0}
.photo{position:absolute}

/* header */
.site-header{position:absolute;left:0;top:0;width:1200px;height:90px;background:var(--white);border-bottom:1px solid var(--line)}
.brand{position:absolute;left:142px;top:16px;display:flex;align-items:center;gap:10px}
.brand-dot{width:54px;height:54px;border-radius:50%;background:var(--blue)}
.brand-name{font:700 24px "Montserrat",sans-serif;color:var(--blue);letter-spacing:.3px}
.topbar{position:absolute;top:12px;left:598px;display:flex;align-items:center;gap:26px;font:500 12px "Montserrat",sans-serif;color:var(--ink)}
.topbar i{display:inline-flex;vertical-align:middle;margin-right:6px}
.topbar .quote{background:#000;color:#fff;padding:0 12px;height:34px;display:flex;align-items:center;font-weight:600;letter-spacing:.5px}
.main-nav{position:absolute;top:60px;left:0;width:1200px;height:16px;font:500 12px "Montserrat",sans-serif;color:var(--ink)}
.main-nav a{position:absolute;transform:translateX(-50%);white-space:nowrap;text-decoration:none;color:inherit}
.main-nav a.active{color:var(--blue);font-weight:600}
.main-nav a.active::after{content:"";position:absolute;left:50%;top:26px;margin-left:-4px;border:4px solid transparent;border-bottom-color:var(--blue)}

/* hero */
.hero{left:0;top:90px;width:1200px;height:480px;background:linear-gradient(180deg,#8fa26a 0%,#5f6e50 35%,#4e4a44 60%,#6f8050 82%,#58683f 100%)}
.hero-title{position:absolute;left:0;top:494px;width:1200px;text-align:center;font:700 40px "Montserrat",sans-serif;color:var(--white);letter-spacing:1px;text-shadow:0 2px 8px rgba(0,0,0,.55)}

/* who we are */
.about-title{left:142px;top:676px;font:700 29px "Montserrat",sans-serif}
.about-title span{color:var(--blue)}
.about-lead{left:142px;top:740px;width:440px;font:400 14px/25px "Open Sans",sans-serif;color:var(--ink)}
.about-lead b{color:var(--blue);font-weight:400}
.about-body{left:142px;top:830px;width:440px;font:400 13px/22.5px "Open Sans",sans-serif;color:var(--text)}
.video{left:613px;top:641px;width:587px;height:437px;background:linear-gradient(160deg,#8d98a6 0%,#6a7685 45%,#9a6f5e 75%,#b8a99a 100%);box-shadow:0 18px 40px rgba(0,0,0,.18)}
.play{position:absolute;left:872px;top:824px}

/* services */
.services-band{left:0;top:1150px;width:1200px;height:295px;background:var(--blue)}
.service{position:absolute;top:1299px;width:440px;height:290px;display:flex;align-items:flex-end;justify-content:center;padding-bottom:18px;text-align:center;font:600 22px/31px "Montserrat",sans-serif;color:var(--white);letter-spacing:.5px;text-shadow:0 2px 6px rgba(0,0,0,.5)}
.service-a{left:151px;background:linear-gradient(180deg,#c7c3bd 0%,#a89478 55%,#4f4535 100%)}
.service-b{left:610px;background:linear-gradient(180deg,#9ec1e0 0%,#a27a5f 50%,#3e3a30 100%)}
.pride-sub{left:0;width:1200px;top:1655px;text-align:center;font:500 19px "Montserrat",sans-serif;color:var(--blue)}
.pride-title{left:0;width:1200px;top:1688px;text-align:center;font:700 31px "Montserrat",sans-serif}

/* gallery */
.gallery{left:0;top:1856px;width:1200px;height:826px;background:var(--pale)}
.feature-card{left:142px;top:2207px;width:451px;height:402px;background:linear-gradient(180deg,#2f87d6 0%,#0f6bbf 100%);color:var(--white);text-align:center}
.feature-card .frame{position:absolute;left:10px;top:12px;right:10px;bottom:12px;border:1px solid rgba(255,255,255,.55)}
.feature-card h3{position:absolute;left:40px;right:40px;top:110px;font:700 19px/32px "Montserrat",sans-serif}
.feature-card p{position:absolute;left:60px;right:60px;top:200px;font:400 13px/21px "Open Sans",sans-serif}

/* why choose */
.why{position:absolute;width:290px;height:234px;background:var(--white);box-shadow:0 4px 18px rgba(0,0,0,.07);text-align:center}
.why .icon{position:absolute;left:50%;top:-40px;margin-left:-48px;width:96px;height:96px;border-radius:50%;background:var(--white);box-shadow:0 4px 14px rgba(0,0,0,.1);display:flex;align-items:center;justify-content:center}
.why .icon.on{background:var(--blue)}
.why h4{position:absolute;left:0;right:0;top:76px;font:700 16.5px "Montserrat",sans-serif;color:var(--blue)}
.why p{position:absolute;left:18px;right:18px;top:108px;font:400 12.5px/25px "Open Sans",sans-serif;color:var(--muted)}

/* banner */
.banner{left:0;top:3546px;width:1200px;height:282px;background:linear-gradient(180deg,#1f6fb7 0%,#0e5fa9 60%,#1a6bb3 100%)}
.banner-sub{left:0;width:1200px;top:3624px;text-align:center;font:500 19px "Montserrat",sans-serif;color:var(--white)}
.banner-title{left:0;width:1200px;top:3654px;text-align:center;font:600 33px "Montserrat",sans-serif;color:var(--white);letter-spacing:1.5px}

/* inquiry */
.field{position:absolute;border:1px solid var(--line);background:var(--white);font:400 11px "Open Sans",sans-serif;color:var(--muted);padding:13px 14px}
.chat{left:988px;top:4274px;width:72px;height:72px;border-radius:50%;background:var(--blue);box-shadow:0 6px 16px rgba(0,0,0,.25);display:flex;align-items:center;justify-content:center;z-index:2}

/* footer */
.footer{left:0;top:4310px;width:1200px;height:438px;background:linear-gradient(180deg,#2a2e33 0%,#1b1e22 70%,#121417 100%)}
.foot-brand{position:absolute;top:4378px;left:0;width:1200px;display:flex;justify-content:center;align-items:center;gap:12px}
.foot-brand .brand-dot{width:66px;height:66px}
.foot-brand .brand-name{color:var(--white);font-size:30px}
.foot-nav{position:absolute;top:4506px;left:0;width:1200px;font:500 13px "Montserrat",sans-serif;color:var(--white)}
.foot-nav span{position:absolute;transform:translateX(-50%);white-space:nowrap}
.foot-col{position:absolute;top:4580px;width:320px;margin-left:-160px;text-align:center;color:var(--white)}
.foot-col h5{margin-top:12px;font:600 12.5px "Montserrat",sans-serif;letter-spacing:.4px}
.foot-col p{margin-top:6px;font:400 12px/19px "Open Sans",sans-serif}
.copy{left:0;top:4748px;width:1200px;height:64px;background:var(--blue)}
.copy p{position:absolute;left:142px;top:24px;font:400 12px "Open Sans",sans-serif;color:var(--white)}
.social{position:absolute;top:20px;width:26px;height:26px;border-radius:50%;border:1.5px solid var(--white);background:rgba(255,255,255,.12)}
</style>
</head>
<body>

<header class="site-header">
  <div class="brand"><span class="brand-dot"></span><span class="brand-name">Brackwell Exteriors</span></div>
  <div class="topbar">
    <span><i><svg width="12" height="12" viewBox="0 0 24 24"><path fill="#0a6cc2" d="M6.6 10.8a15 15 0 0 0 6.6 6.6l2.2-2.2c.3-.3.7-.4 1-.2 1.1.4 2.3.6 3.6.6.6 0 1 .4 1 1V20c0 .6-.4 1-1 1A17 17 0 0 1 3 4c0-.6.4-1 1-1h3.5c.6 0 1 .4 1 1 0 1.3.2 2.5.6 3.6.1.3 0 .7-.2 1z"/></svg></i>+1 780-555-0174</span>
    <span><i><svg width="14" height="11" viewBox="0 0 24 18"><rect width="24" height="18" rx="2" fill="#0a6cc2"/><path d="M2 2l10 8 10-8" stroke="#fff" stroke-width="2" fill="none"/></svg></i>info@brackwellbuilders.ca</span>
    <span class="quote">REQUEST A QUOTE</span>
  </div>
  <nav class="main-nav">
    <a class="active" style="left:528px">HOME</a>
    <a style="left:630px">ABOUT US</a>
    <a style="left:744px">SERVICES</a>
    <a style="left:876px">MEET THE TEAM</a>
    <a style="left:1018px">CONTACT US</a>
  </nav>
</header>

<div class="photo hero" role="img" aria-label="Modern two-storey home with wood garage door and landscaped front yard"></div>
<h1 class="hero-title">EXPERIENCE THE BRACKWELL DIFFERENCE</h1>

<section>
  <h2 class="abs about-title">WHO <span>WE ARE</span></h2>
  <p class="abs about-lead"><b>Brackwell</b> Exteriors is dolor sit amet, consectetuer adipiaelitsed diam nonummy nibh euismod tincidunt ut laoreet dolore loreil magna aliquam erat volutpat. Ut wisi enim ad minim.</p>
  <p class="abs about-body">Lorem ipsum dolor sit amet, consectetuer adipiscing elit, sed diamsal nonummy nibh euismod tincidunt ut laoreet dolore magna aliquamas erat volutpat. Ut wisi enim ad minim veniam, quis nostrud exercicesas tation ullamcorper suscipit lobortis nisl ut aliquip ex ea commodo oftii consequat. Duis autem vel eum iriure dolor in hendrerit in vulputateen velit esse molestie consequat.</p>
  <span class="btn btn-solid" style="left:142px;top:986px;width:140px">Learn More</span>
  <span class="btn btn-line" style="left:297px;top:986px;width:140px">Watch Video</span>
  <svg class="abs" style="left:436px;top:995px" width="152" height="50" viewBox="0 0 152 50"><path d="M2 36 C 50 56, 110 50, 146 8" stroke="#9aa3ad" stroke-width="1" stroke-dasharray="3 3" fill="none"/><path d="M140 8 L147 6 L146 14" stroke="#0a6cc2" stroke-width="1.2" fill="none"/></svg>
  <div class="photo video" role="img" aria-label="Video still of a house exterior under renovation with scaffolding"></div>
  <svg class="play" width="72" height="72" viewBox="0 0 72 72"><circle cx="36" cy="36" r="34" fill="#fff" stroke="rgba(255,255,255,.5)" stroke-width="4"/><path d="M29 24 L50 36 L29 48 Z" fill="#0a6cc2"/></svg>
</section>

<section>
  <div class="abs services-band"></div>
  <h2 class="heading" style="top:1222px;color:#fff">OUR SERVICES</h2>
  <div class="service service-a" role="img" aria-label="House exterior with scaffolding during renovation">EXTERIOR<br>RENOVATIONS</div>
  <div class="service service-b" role="img" aria-label="Newly built two-storey house with attached garage">DETACHED GARAGE<br>CONSTRUCTION</div>
  <p class="abs pride-sub">Honest And Reliable Construction Service In Edmonton And Area.</p>
  <h2 class="abs pride-title">We Take Pride In Each And Every Project</h2>
  <span class="btn btn-line" style="left:432px;top:1748px;width:150px">Request a Quote</span>
  <span class="btn btn-solid" style="left:600px;top:1748px;width:170px">Contact Us Today</span>
</section>

<section>
  <div class="abs gallery"></div>
  <h2 class="heading" style="top:1926px">WORK <span>GALLERY</span></h2>
  <div class="photo" style="left:142px;top:2000px;width:217px;height:192px;background:linear-gradient(180deg,#b9c0c6,#6b5b4a 60%,#8a7a64)" role="img" aria-label="House under construction with stone facade"></div>
  <div class="photo" style="left:374px;top:2000px;width:219px;height:192px;background:linear-gradient(180deg,#f7f7f7,#e6e6e6)" role="img" aria-label="Floor plan drawing"></div>
  <div class="photo" style="left:607px;top:2000px;width:451px;height:400px;background:linear-gradient(180deg,#3a5a86 0%,#7a7f8a 40%,#8a5a35 70%,#3f5a2c 100%)" role="img" aria-label="Modern home lit at dusk with fire pit on the lawn"></div>
  <div class="abs feature-card" role="img" aria-label="Blue-tinted house photo behind text">
    <div class="frame"></div>
    <h3>Unrivalled Quality and Attention to Detail Turning Dreams into Reality</h3>
    <p>Lorem ipsum dolor sit amet, ipsu, ofte consectetuer adipiscing elit, sed diam nonummy nibh euismod tincidunt ut laoreet dolore magna aliquam erat volutpat Ut wisi enim...</p>
  </div>
  <div class="photo" style="left:607px;top:2417px;width:217px;height:192px;background:linear-gradient(135deg,#d9c4a6,#a7825a 55%,#6b5038)" role="img" aria-label="Wooden staircase framing"></div>
  <div class="photo" style="left:841px;top:2417px;width:217px;height:192px;background:linear-gradient(180deg,#e6e6e4,#a9a59f 60%,#7b7670)" role="img" aria-label="Finished kitchen with island"></div>
</section>

<section>
  <h2 class="heading" style="top:2750px">WHY CHOOSE <span>US?</span></h2>

  <div class="why" style="left:142px;top:2875px">
    <div class="icon"><svg width="40" height="40" viewBox="0 0 40 40" fill="none" stroke="#0a6cc2" stroke-width="1.6"><path d="M20 5l4 8 9 1-6.5 6 1.5 9-8-4.5-8 4.5 1.5-9L7 14l9-1z"/></svg></div>
    <h4>CERTIFIED EXPERIENCE</h4>
    <p>Having professionals do the job gives you the confidence that the job will be done right, on budget, and on time.</p>
  </div>
  <div class="why" style="left:454px;top:2875px">
    <div class="icon"><svg width="40" height="40" viewBox="0 0 40 40" fill="none" stroke="#0a6cc2" stroke-width="1.6"><rect x="6" y="6" width="20" height="14" rx="6"/><rect x="16" y="14" width="18" height="12" rx="6"/><circle cx="12" cy="32" r="3"/><circle cx="20" cy="32" r="3"/><circle cx="28" cy="32" r="3"/></svg></div>
    <h4>SUPERIOR COMMUNICATION</h4>
    <p>Taking the time to explain the construction process and promptly answering the phone or email is what sets us apart from others.</p>
  </div>
  <div class="why" style="left:768px;top:2875px">
    <div class="icon"><svg width="40" height="40" viewBox="0 0 40 40" fill="none" stroke="#0a6cc2" stroke-width="1.6"><circle cx="20" cy="14" r="9"/><path d="M20 9v10M17 11h5M17 17h5"/><path d="M5 30h8l6 3h10l6-5"/></svg></div>
    <h4>COMPETITIVE PRICING</h4>
    <p>Although we offer the best in services, we won't blow your budget on the job. We also take credit cards in our renovations division.</p>
  </div>

  <div class="why" style="left:142px;top:3180px">
    <div class="icon"><svg width="40" height="40" viewBox="0 0 40 40" fill="none" stroke="#0a6cc2" stroke-width="1.6"><rect x="7" y="8" width="22" height="26"/><path d="M11 15h14M11 21h10M11 27h8"/><circle cx="30" cy="27" r="5"/></svg></div>
    <h4>GUARANTEED SATISFACTION</h4>
    <p>We aren't happy unless you are. Along with a robust limited lifetime warranty on our work, we ensure you are satisfied even years after completion.</p>
  </div>
  <div class="why" style="left:454px;top:3180px">
    <div class="icon on"><svg width="42" height="42" viewBox="0 0 40 40" fill="none" stroke="#fff" stroke-width="1.8"><path d="M20 6l11 4v8c0 8-5 13-11 16-6-3-11-8-11-16v-8z"/><path d="M15 20l4 4 7-8"/></svg></div>
    <h4>SAFETY CONSCIENCE</h4>
    <p>COR certification, liability insurance, and WCB coverage on all workers gives you peace of mind that the job will be done safely.</p>
  </div>
  <div class="why" style="left:768px;top:3180px">
    <div class="icon"><svg width="40" height="40" viewBox="0 0 40 40" fill="none" stroke="#0a6cc2" stroke-width="1.6"><circle cx="15" cy="15" r="7"/><circle cx="15" cy="15" r="2.5"/><path d="M22 22l10 3v6c0 3-4 5-6 6-2-1-6-3-6-6z"/></svg></div>
    <h4>UNRIVALLED QUALITY</h4>
    <p>Our greatest asset is our unrivalled pursuit of a "top of the line" job each and every time.</p>
  </div>

  <span class="btn btn-solid" style="left:515px;top:3437px;width:170px">Contact Us Today</span>
</section>

<section>
  <div class="photo banner" role="img" aria-label="Blue-tinted photo of a house with a detached garage"></div>
  <p class="abs banner-sub">Lorem ipsum dolor sit amet, ipsum often consectetuer adipiscing elit</p>
  <h2 class="abs banner-title">DETACHED GARAGE CONSTRUCTION</h2>
  <span class="btn btn-line" style="left:426px;top:3716px;width:158px">Request a Quote</span>
  <span class="btn" style="left:597px;top:3716px;width:170px;background:#fff;color:var(--blue)">Contact Us Today</span>
</section>

<section>
  <h2 class="heading" style="top:3898px">QUICK <span>INQUIRY</span></h2>
  <div class="field" style="left:202px;top:3968px;width:387px;height:43px">Name*</div>
  <div class="field" style="left:611px;top:3968px;width:387px;height:43px">Phone*</div>
  <div class="field" style="left:202px;top:4024px;width:387px;height:43px">Email*</div>
  <div class="field" style="left:611px;top:4024px;width:387px;height:43px">Choose a Service
    <svg style="position:absolute;right:14px;top:18px" width="8" height="5" viewBox="0 0 8 5"><path d="M0 0l4 4 4-4" stroke="#555" fill="none"/></svg></div>
  <div class="field" style="left:202px;top:4080px;width:796px;height:96px">Message*</div>
  <span class="btn btn-solid" style="left:536px;top:4200px;width:128px">Submit</span>
  <div class="abs chat"><svg width="32" height="32" viewBox="0 0 32 32" fill="none" stroke="#fff" stroke-width="1.8"><path d="M5 14a9 8 0 1 1 4 7l-4 2 1-4"/><path d="M16 22a8 7 0 0 0 12-2l1 5-4-2"/></svg></div>
</section>

<footer>
  <div class="photo footer" role="img" aria-label="Dark city skyline at night"></div>
  <div class="foot-brand"><span class="brand-dot"></span><span class="brand-name">Brackwell Exteriors</span></div>
  <div class="foot-nav">
    <span style="left:328px">HOME</span>
    <span style="left:436px">ABOUT US</span>
    <span style="left:556px">SERVICES</span>
    <span style="left:697px">MEET THE TEAM</span>
    <span style="left:848px">CONTACT US</span>
  </div>
  <div class="foot-col" style="left:286px">
    <svg width="26" height="44" viewBox="0 0 26 44" fill="none" stroke="#fff" stroke-width="1.5"><rect x="2" y="2" width="22" height="40" rx="3"/><path d="M2 8h22M2 35h22"/><circle cx="13" cy="38.5" r="1.5"/></svg>
    <h5>PHONE</h5>
    <p>+1 780-555-0174</p>
  </div>
  <div class="foot-col" style="left:600px">
    <svg width="32" height="44" viewBox="0 0 32 44" fill="none" stroke="#fff" stroke-width="1.5"><path d="M16 42C8 30 3 22 3 15a13 13 0 0 1 26 0c0 7-5 15-13 27z"/><circle cx="16" cy="15" r="5"/></svg>
    <h5>BRACKWELL EXTERIORS</h5>
    <p>4820 Lindell Rd #118, Sherwood<br>Park, AB T8B 2J4, Canada</p>
  </div>
  <div class="foot-col" style="left:914px">
    <svg width="46" height="44" viewBox="0 0 46 44" fill="none" stroke="#fff" stroke-width="1.5"><rect x="2" y="8" width="42" height="30"/><path d="M2 8l21 17 21-17M2 38l16-15M44 38L28 23"/></svg>
    <h5>EMAIL</h5>
    <p>info@brackwellbuilders.ca</p>
  </div>
  <div class="abs copy">
    <p>Copyright © 2020 BRACKWELL EXTERIORS. All Rights Reserved.</p>
    <span class="social" style="left:920px"></span>
    <span class="social" style="left:957px"></span>
    <span class="social" style="left:994px"></span>
    <span class="social" style="left:1031px"></span>
  </div>
</footer>

</body>
</html>
```